Property Services Company Needs a Brochure Design

Looking for a new brochure design for an existing property services company.

We provide a range of property services from, market research, real estate brokerage, valuation and appraisal, property development and other real estate consulting services.

We would like a fresh modern brochure design with good graphics and features. Our colours are white, blue and orange.

The design should communicate, attention to detail, superior service delivery and distinction in results.
Updates

I would like the brochure to be roughly about 20 pages.

Containing the following,

1) An introduction
2) Contents Page
2) What we do
3) Our Services
4) Agency & Brokerage
5) Real Estate Consulting
6) Market Research
7) Appraisal & Valuation
8) Project Management
9) Property Development

I would also like icons to represent items 4,5,6,7,8 & 9, they should be represented vertically on each of the pages from the contents page and highlighted individually on the pages that they represent.. i.e. on appraisal & valuation page, all six icons will be arranged vertically and the appraisal and valuations icon will be highlighted.

I will also like to have images that depict the services on the various pages.

I have some pages I think will flow which I will upload shortly.

Industry/Entity Type

Real Estate

Font styles to use
Serif

Colors
f78f20
0455a3

```html
<!DOCTYPE html>
<html lang="en">
<head>
<meta charset="utf-8">
<title>Larkvale Property Services – Services Spread</title>
<link rel="stylesheet" href="https://fonts.googleapis.com/css2?family=Tinos:wght@400;700&display=swap">
<style>
  :root {
    --navy: #2b2262;
    --orange: #e25f10;
    --ink: #1e1e1e;
    --paper: #ffffff;
    --backdrop: #f4f4f4;
    --frame: #555555;
  }
  * { margin: 0; padding: 0; box-sizing: border-box; }
  html, body {
    width: 1200px; height: 864px; overflow: hidden;
    background: var(--backdrop);
  }
  .spread {
    position: relative; width: 1200px; height: 864px;
    font-family: "Tinos", "Times New Roman", serif;
    color: var(--ink);
  }
  .sheet {
    position: absolute; left: 40px; top: 35px; width: 1120px; height: 793px;
    background: var(--paper); border: 1px solid var(--frame);
  }
  .fold {
    position: absolute; left: 600px; top: 35px; width: 1px; height: 793px;
    background: var(--frame); z-index: 5;
  }
  .band { position: absolute; }
  .band--navy { background: var(--navy); }
  .band--orange { background: var(--orange); }

  .photo { position: absolute; }
  .photo--reader { left: 331px; top: 35px; width: 269px; height: 220px;
    background: linear-gradient(160deg, #e9e8e4 0%, #cfc9c0 45%, #3a4660 75%, #bdb8b0 100%); }
  .photo--engineer { left: 40px; top: 622px; width: 255px; height: 206px;
    background: linear-gradient(120deg, #4a4c50 0%, #8e8f8c 30%, #e6e4dc 60%, #f2efe6 100%); }
  .photo--edge { left: 600px; top: 35px; width: 60px; height: 220px;
    background: linear-gradient(90deg, #e8e3dc, #f6f4f0); }
  .photo--site { left: 888px; top: 35px; width: 272px; height: 180px;
    background: linear-gradient(135deg, #6fa7d8 0%, #9ec9ea 35%, #c8b13a 55%, #3e4a58 80%, #9aa6b0 100%); }
  .photo--office { left: 600px; top: 475px; width: 560px; height: 353px;
    background: linear-gradient(100deg, #4c4f55 0%, #a9acb0 22%, #dfe1e3 50%, #f3f4f5 75%, #d6d8da 100%); }

  .title-box {
    position: absolute; left: 96px; top: 103px; width: 196px; height: 37px;
    border: 1px solid var(--navy); border-left: none; border-radius: 0 10px 10px 0;
  }
  .title-box::after {
    content: ""; position: absolute; left: -1px; top: 3px; right: 3px; bottom: 3px;
    border: 1px solid var(--navy); border-left: none; border-radius: 0 7px 7px 0;
  }
  .title-box h1 {
    position: absolute; left: 28px; top: 4px;
    font-size: 25px; font-weight: 700; color: var(--navy); letter-spacing: 0.3px;
  }

  .column { position: absolute; font-size: 12.2px; line-height: 14.85px; }
  .column h2 { font-size: 13.2px; font-weight: 700; color: var(--navy); line-height: 16px; margin-bottom: 2px; }
  .column p + h2 { margin-top: 4px; }
  .column .accent { color: var(--orange); }
  .column .what-we-do { color: var(--orange); text-decoration: underline; font-size: 14px; margin-top: 8px; font-weight: 400; }
  .column p + p { margin-top: 5px; }

  .column--one { left: 123px; top: 158px; width: 175px; }
  .column--two { left: 332px; top: 273px; width: 200px; }
  .column--three { left: 683px; top: 115px; width: 198px; }
  .column--four { left: 888px; top: 233px; width: 210px; }
</style>
</head>
<body>
<div class="spread">
  <div class="sheet"></div>

  <div class="band band--navy" style="left:40px; top:35px; width:56px; height:587px;"></div>
  <div class="band band--orange" style="left:540px; top:255px; width:60px; height:573px;"></div>
  <div class="band band--navy" style="left:600px; top:255px; width:60px; height:220px;"></div>
  <div class="band band--orange" style="left:1103px; top:215px; width:57px; height:260px;"></div>

  <div class="photo photo--reader" role="img" aria-label="Businessman in a suit smiling while reading a newspaper on a sofa"></div>
  <div class="photo photo--engineer" role="img" aria-label="Engineer in a yellow hard hat studying a large plan"></div>
  <div class="photo photo--edge" role="img" aria-label="Soft light office interior detail"></div>
  <div class="photo photo--site" role="img" aria-label="Three workers in hard hats and safety vests reviewing plans on site"></div>
  <div class="photo photo--office" role="img" aria-label="Modern office with glass desk, black chair and dark cabinets"></div>

  <div class="fold"></div>

  <div class="title-box"><h1>SERVICES</h1></div>

  <section class="column column--one">
    <h2>Agency&amp; Brokerage</h2>
    <p>The brokerage team, covers both landlords and tenants across the residential and commercial markets. With a large database of industry specific individuals and corporate twinned with a large database of inventory, we are able to very quickly understand the needs of our clients and find the perfect fit. We enjoy long standing relationships with many of our clients and landlords, and are always happy to meet with new clients to advise on how best to maximize their rental return or budget.</p>
    <h2>Consulting</h2>
    <p>We provide a broad range of consulting services, we understand that out client needs may vary and our experienced team are at hand to provide tailored solutions to their needs. Our professional services include corporate planning, feasibility studies, market studies, due diligence, property tax, litigation, asset review and framework for foreign direct investment.</p>
  </section>

  <section class="column column--two">
    <h2>Market Research</h2>
    <p>Our market research team, regularly conduct surveys across a wide range of areas in both the commercial and residential markets. They regularly produce market reports that can be used for a wide range of purposes. This information also provides our team members with superior knowledge of market trends, price shifts, occupancy rates and other unique trends. The information provided allows us to provide information useful for forecasting growth and trends in the market.</p>
    <h2>Project Management&amp; Property Development</h2>
    <p>Our project management team, with vast experience across commercial and residential developments provide the much needed support to achieve your dream property or office, allowing our clients to concentrate on their core business. We provide accurate information from financing, to design concept to budgeting and construction management. We take pride in creating inspirational developments that people can live, work and enjoy, whilst adding value.</p>
  </section>

  <section class="column column--three">
    <h2 class="accent">Valuation &amp; Appraisal</h2>
    <p>We provide valuation and appraisal services to clients across a broad spectrum. Our valuation advice can provide information to assist with portfolio valuation, single asset valuation, financial reporting valuation. These services are provided to individuals, financial institutions and corporates. Appraisal methods will vary based on the specific needs of our clients</p>
    <h2 class="what-we-do">WHAT WE DO</h2>
    <p>Larkvale is a leading property services company, incorporated in 1984, providing bespoke solutions in advisory, brokerage and turnkey solutions to owners, occupiers and property investors. Over the years we have expanded</p>
  </section>

  <section class="column column--four">
    <p>our services with a foundation based on core strengths, unrivalled local expertise, network and knowledge combined with strategic partnership. As well as providing property solutions we also develop commercial and residential units.</p>
    <p>Our growth has been based on maintaining relationships with our extensive client base,</p>
    <p>ranging from financial institutions, government agencies, airlines and servicing companies, manufacturing companies, multinationals and local</p>
  </section>
</div>
</body>
</html>
```